Professional Engineering Web Design

Project Brief: Website Redesign for Mechanical Design Consultancy
Project Overview
I want to update and improve my current website to create a more professional, modern, and high-credibility online presence for my mechanical design consultancy.

Current site: https://valtorix.design/

The new website must communicate expertise, precision, and trust—matching the standard of top engineering and product design agencies.

Reference Websites (Style + Structure Inspiration)
These represent the quality, cleanliness, and professionalism I want to achieve:

https://plinthwaredesign.com/
https://www.sorvane.com/
https://bramlow-uk.com/
Brand Look
Professional, modern, engineering-focused aesthetic
Clean layouts and strong typography
High-quality imagery conveying precision, innovation, and mechanical expertise
Colour scheme and styling must follow my existing logo (attached in project)
Platform Requirements
The website must be built on WordPress
Should use a clean, flexible theme or modern page builder (Elementor, Gutenberg, Bricks, or similar)
Avoid overly complex custom coding so I can easily edit content later
Final deliverable must allow me to manage and update content without developer assistance
Functionality
Fast-loading, lightweight, and smooth user experience
Clean animations and transitions similar to the reference sites
Fully mobile responsive
Clear navigation and strong visual hierarchy
Contact forms optimised for lead generation
Optional: subtle scroll effects, case study sliders, icon animations, etc.
SEO Aspirations
Developer should recommend and implement a modern SEO strategy
Proper on-page SEO setup (titles, meta, schema, alt tags, heading structure)
Optimised site architecture for ranking and crawling
Aim: Generate leads through improved visibility and keyword targeting
Optional but useful: Google Analytics, Google Search Console setup
User Journeys
(Recommended structure)

The site should be crafted around clear, intuitive journeys for each type of visitor:

Potential new clients
Quickly understand what services I offer
View examples of past work / case studies
See credibility indicators (process, expertise, industries served)
Easily contact me or request a project discussion
Returning clients
Access updated portfolio items
Find contact details or book follow-up work easily
General visitors discovering through SEO
Be guided to valtorix service areas
Understand my value proposition quickly
Be invited to learn more or make contact
The developer should design the structure to support these journeys smoothly.

Maintenance Expectations
Website will be maintained by me, so it should be easy to update using relatively basic WordPress skills
Use modular templates and simple backend structure
Avoid unnecessary plugins
Provide brief handover documentation if required
Hosting Preferences
Site is currently hosted via a family member
Open to discussing moving to a paid, reliable hosting provider if preferable for performance and maintainability
Developer may advise on the best hosting setup for WordPress
Content
Most content can be taken from the existing website
Developer is welcome to suggest improvements to structure, layout, and imagery
Must remain easy for me to edit or add new content later (e.g., new projects)
Deliverables
Fully built WordPress website
Clean, professional, modern design inspired by the reference sites
Mobile-responsive across all devices
SEO-ready structure and optimisations
Transfer of website and admin rights
Any design assets, templates, or documentation used

```html
<!DOCTYPE html>
<html lang="en">
<head>
<meta charset="utf-8">
<title>Valtorix Mechanical Design</title>
<link rel="stylesheet" href="https://fonts.googleapis.com/css2?family=Arimo:ital,wght@0,400;0,700;1,400&display=swap">
<style>
:root{
  --blue:#2f5ff2;
  --ink:#1c1c1e;
  --text:#4a4a4f;
  --grey-bg:#e9e9ee;
  --card:#ffffff;
  --soft:#f1f1f4;
  --star:#f5b400;
}
*{margin:0;padding:0;box-sizing:border-box}
html,body{width:1200px;height:3923px;overflow:hidden}
body{position:relative;font-family:"Arimo",Arial,sans-serif;color:var(--ink);background:#fff}
.abs{position:absolute}
.center{text-align:center}

/* header */
.hero{left:0;top:0;width:1200px;height:640px;background:linear-gradient(180deg,#dedee6 0%,#e6e6ec 45%,#d3d3db 75%,#c6c6cf 100%)}
.hero-art{left:0;top:330px;width:1200px;height:310px;background:linear-gradient(160deg,rgba(255,255,255,.0) 0%,rgba(250,250,252,.7) 40%,rgba(190,190,200,.6) 100%)}
.logo{left:143px;top:14px;display:flex;align-items:center;gap:8px}
.logo-dot{width:46px;height:46px;border-radius:50%;background:var(--blue)}
.logo-name{font-size:30px;font-weight:700;letter-spacing:4px;color:#333}
.nav-active{left:396px;top:0;width:40px;height:4px;background:var(--blue)}
.nav{top:30px;left:396px;display:flex;align-items:center;font-size:14px;color:#333}
.nav span.sep{width:3px;height:10px;background:var(--blue);margin:0 29px}
.phone{left:890px;top:22px;display:flex;align-items:center;gap:9px;font-size:14px;color:#333}
.phone-ic{width:30px;height:30px;border-radius:50%;background:var(--blue);display:flex;align-items:center;justify-content:center}
.hero-title{left:0;width:1200px;top:234px;font-size:48px;font-weight:700}
.hero-sub{left:0;width:1200px;top:295px;font-size:32px}
.scroll{left:0;width:1200px;top:577px;font-size:11px}

/* welcome */
.welcome{left:0;top:640px;width:1200px;height:201px;background:var(--blue);color:#fff}
.welcome-small{left:143px;top:45px;font-size:20px;font-weight:700}
.welcome-title{left:143px;top:70px;font-size:36px;font-weight:700;line-height:37px}
.welcome-rule{left:486px;top:63px;width:2px;height:70px;background:#fff}
.welcome-text{left:530px;top:62px;width:530px;font-size:15.5px;line-height:24px}

/* expertise */
.section-title{left:0;width:1200px;font-size:48px;font-weight:700}
.exp-card{top:1014px;width:291px;height:361px;background:var(--card);border-radius:14px;box-shadow:0 8px 30px rgba(0,0,0,.07);text-align:center}
.exp-card h3{margin-top:42px;font-size:20px;line-height:28px}
.exp-card p{margin:14px auto 0;width:230px;font-size:15px;line-height:24px;color:var(--text)}
.exp-icon{position:absolute;left:86px;top:203px;width:118px;height:118px;border-radius:50%;background:#e9e9ed;display:flex;align-items:center;justify-content:center}

/* work */
.work{left:0;top:1503px;width:1200px;height:800px;border-radius:150px;background:linear-gradient(180deg,#e6e6eb,#ececf0 60%,#e4e4e9)}
.work-sub{left:0;width:1200px;top:1666px;font-size:20px;font-weight:700}
.slide{top:1729px;height:457px;width:107px;background:#fff;border-radius:12px;display:flex;align-items:center;justify-content:center}
.slide span{transform:rotate(-90deg);white-space:nowrap;font-size:19px;font-weight:700}
.slide-active{left:539px;top:1727px;width:384px;height:460px;background:#fff;border:3px solid var(--blue);border-radius:14px}
.slide-photo{position:absolute;left:80px;top:40px;width:220px;height:320px;border-radius:6px;background:linear-gradient(180deg,#8c979c,#5e6a70 60%,#4c575c)}
.slide-label{position:absolute;left:0;width:100%;bottom:40px;text-align:center;color:var(--blue);font-size:19px;font-weight:700}

/* about */
.ring{left:680px;top:2440px;width:520px;height:560px}
.photo-frame{left:125px;top:2402px;width:493px;height:507px;border:3px solid #e4e4e8;border-radius:40px}
.photo{left:143px;top:2420px;width:457px;height:471px;border-radius:32px;background:linear-gradient(160deg,#6c8a4e 0%,#9a8e72 35%,#2e3f5c 75%,#1f2d47 100%)}
.about-card{left:533px;top:2463px;width:522px;height:382px;background:#fff;border-radius:28px;box-shadow:0 8px 30px rgba(0,0,0,.07)}
.about-card h2{position:absolute;left:41px;top:45px;font-size:48px}
.about-card p{position:absolute;left:41px;top:117px;width:460px;font-size:15.5px;line-height:24px;color:var(--text)}
.btn{position:absolute;left:41px;top:271px;width:271px;height:61px;border-radius:31px;background:var(--blue);color:#fff;font-size:16px;font-weight:700;display:flex;align-items:center;justify-content:center}

/* testimonials */
.testi-title{left:0;width:1200px;top:3016px;font-size:48px;font-weight:700;line-height:57px}
.stars{left:0;width:1200px;top:3160px;display:flex;justify-content:center;gap:6px}
.quote{left:280px;width:640px;top:3196px;font-size:16.5px;line-height:24px;font-style:italic;color:var(--text)}
.avatar{left:532px;top:3349px;width:62px;height:62px;border-radius:50%;border:2px solid #333;background:linear-gradient(180deg,#b89a84,#6c5a4e)}
.author{left:601px;top:3356px;font-size:20px;font-weight:700}
.role{left:601px;top:3384px;font-size:15px;color:var(--text)}
.arrow{width:30px;height:40px}

/* footer */
.footer{left:0;top:3523px;width:1200px;height:400px;border-radius:150px 150px 0 0;background:linear-gradient(180deg,#e5e5ea,#ececf0)}
.contact-ic{width:76px;height:76px;border-radius:50%;background:var(--blue);display:flex;align-items:center;justify-content:center}
.contact-label{font-size:24px;font-weight:700}
.contact-text{font-size:16px;line-height:24px;color:var(--text)}
.foot-nav{left:0;top:3762px;width:1200px;height:41px;background:rgba(255,255,255,.75);display:flex;align-items:center;justify-content:center;font-size:17px;color:#333}
.foot-nav span.sep{width:3px;height:10px;background:var(--blue);margin:0 36px}
.copy{left:0;width:1200px;top:3843px;font-size:17px;color:#444}
.up{left:1016px;top:3833px;width:40px;height:40px;border-radius:50%;background:var(--blue);display:flex;align-items:center;justify-content:center}
</style>
</head>
<body>

<!-- Header / hero -->
<section class="abs hero">
  <div class="abs hero-art" role="img" aria-label="Soft white 3D render of flowing curved ribbon forms"></div>
</section>
<div class="abs logo"><span class="logo-dot"></span><span class="logo-name">valtorix</span></div>
<div class="abs nav-active"></div>
<nav class="abs nav"><span>Home</span><span class="sep"></span><span>Portfolio</span><span class="sep"></span><span>Our Services</span><span class="sep"></span><span>Contact Us</span></nav>
<div class="abs phone">
  <span class="phone-ic"><svg width="14" height="14" viewBox="0 0 24 24"><path fill="#fff" d="M6.6 10.8a15 15 0 0 0 6.6 6.6l2.2-2.2a1 1 0 0 1 1-.25 11.4 11.4 0 0 0 3.6.57 1 1 0 0 1 1 1V20a1 1 0 0 1-1 1A17 17 0 0 1 3 4a1 1 0 0 1 1-1h3.5a1 1 0 0 1 1 1c0 1.25.2 2.45.57 3.57a1 1 0 0 1-.25 1z"/></svg></span>
  <span>+44 (0) 7900 314 622</span>
</div>
<h1 class="abs hero-title center">Mechanical CAD Design</h1>
<p class="abs hero-sub center">Cutting Edge Engineering</p>
<div class="abs scroll center">Scroll To Explore<br>
  <svg width="12" height="8" viewBox="0 0 12 8"><path d="M1 1l5 5 5-5" stroke="#222" stroke-width="2" fill="none"/></svg></div>

<!-- Welcome band -->
<section class="abs welcome">
  <div class="abs welcome-small">Welcome to</div>
  <h2 class="abs welcome-title">Valtorix Mechanical<br>Design</h2>
  <div class="abs welcome-rule"></div>
  <p class="abs welcome-text">We are a UK based design consultancy offering a comprehensive mechanical and product design service from initial concepts through to full volume production.</p>
</section>

<!-- Expertise -->
<h2 class="abs section-title center" style="top:940px">Our Expertise</h2>
<article class="abs exp-card" style="left:143px">
  <h3>Bespoke<br>Product Design</h3>
  <p>Innovative design from concept through the full development life cycle</p>
  <div class="exp-icon"><svg width="48" height="48" viewBox="0 0 48 48"><rect x="4" y="18" width="22" height="22" rx="2" fill="var(--blue)"/><rect x="20" y="6" width="22" height="22" rx="2" fill="#4a74f5"/></svg></div>
</article>
<article class="abs exp-card" style="left:455px">
  <h3>3D Modelling and<br>Drawings</h3>
  <p>We create 3D CAD, 2D engineering drawings and photorealistic renders</p>
  <div class="exp-icon"><svg width="48" height="48" viewBox="0 0 48 48"><path d="M24 4l18 10-18 10L6 14z" fill="#5b82f7"/><path d="M6 14l18 10v20L6 34z" fill="var(--blue)"/><path d="M42 14L24 24v20l18-10z" fill="#2449c7"/></svg></div>
</article>
<article class="abs exp-card" style="left:766px">
  <h3>Design for<br>Manufacture</h3>
  <p>Creating designs optimised for prototype and production manufacture</p>
  <div class="exp-icon"><svg width="60" height="56" viewBox="0 0 60 56"><circle cx="22" cy="32" r="13" fill="none" stroke="var(--blue)" stroke-width="8" stroke-dasharray="5 3"/><circle cx="40" cy="16" r="9" fill="none" stroke="var(--blue)" stroke-width="6" stroke-dasharray="4 3"/><circle cx="44" cy="42" r="7" fill="none" stroke="var(--blue)" stroke-width="5" stroke-dasharray="3 3"/></svg></div>
</article>

<!-- Work -->
<section class="abs work" role="img" aria-label="Light grey background with faint hexagon pattern"></section>
<h2 class="abs section-title center" style="top:1590px">Our Work</h2>
<p class="abs work-sub center">A small selection of our previous projects</p>
<div class="abs slide" style="left:143px"><span>3-Piece Alloy Wheels</span></div>
<div class="abs slide" style="left:276px"><span>Go-Kart Simulator Design</span></div>
<div class="abs slide" style="left:408px"><span>Design for Manufacture</span></div>
<div class="abs slide-active">
  <div class="slide-photo" role="img" aria-label="Photo of a grey electrical switchgear cabinet"></div>
  <div class="slide-label">Electrical Switchgear</div>
</div>
<div class="abs slide" style="left:950px"><span>Orvi Luxury Pen</span></div>
<svg class="abs arrow" style="left:56px;top:1934px" viewBox="0 0 30 40"><path d="M22 4L8 20l14 16" stroke="#222" stroke-width="6" fill="none"/></svg>
<svg class="abs arrow" style="left:1113px;top:1934px" viewBox="0 0 30 40"><path d="M8 4l14 16L8 36" stroke="var(--blue)" stroke-width="6" fill="none"/></svg>

<!-- About -->
<svg class="abs ring" viewBox="0 0 520 560"><circle cx="240" cy="260" r="220" fill="none" stroke="#eef0f8" stroke-width="70"/></svg>
<div class="abs photo-frame"></div>
<div class="abs photo" role="img" aria-label="Portrait photo of the chief engineer outdoors"></div>
<section class="abs about-card">
  <h2>About Us</h2>
  <p>Rowan Pryce is the Chief Engineer at Valtorix Mechanical Design. He has 11 years experience working as a mechanical design engineer in multiple industries including high performance automotive, consumer products, medical, industrial plus many more. He has worked in multiple roles across a wide range of products.</p>
  <div class="btn">Tell us about your ideas</div>
</section>

<!-- Testimonials -->
<h2 class="abs testi-title center">What Our Customers<br>Say About Us</h2>
<div class="abs stars">
  <svg width="17" height="16" viewBox="0 0 24 23"><path d="M12 0l3.7 7.5 8.3 1.2-6 5.8 1.4 8.3L12 18.9l-7.4 3.9L6 14.5 0 8.7l8.3-1.2z" fill="var(--star)"/></svg>
  <svg width="17" height="16" viewBox="0 0 24 23"><path d="M12 0l3.7 7.5 8.3 1.2-6 5.8 1.4 8.3L12 18.9l-7.4 3.9L6 14.5 0 8.7l8.3-1.2z" fill="var(--star)"/></svg>
  <svg width="17" height="16" viewBox="0 0 24 23"><path d="M12 0l3.7 7.5 8.3 1.2-6 5.8 1.4 8.3L12 18.9l-7.4 3.9L6 14.5 0 8.7l8.3-1.2z" fill="var(--star)"/></svg>
  <svg width="17" height="16" viewBox="0 0 24 23"><path d="M12 0l3.7 7.5 8.3 1.2-6 5.8 1.4 8.3L12 18.9l-7.4 3.9L6 14.5 0 8.7l8.3-1.2z" fill="var(--star)"/></svg>
  <svg width="17" height="16" viewBox="0 0 24 23"><path d="M12 0l3.7 7.5 8.3 1.2-6 5.8 1.4 8.3L12 18.9l-7.4 3.9L6 14.5 0 8.7l8.3-1.2z" fill="var(--star)"/></svg>
</div>
<p class="abs quote center">"Rowan was an excellent teammate on my project. He leveraged his considerable knowledge to make valuable recommendations and guide the design process effectively. He was flexible with multiple revisions, regularly available to discuss problems we were working through, and stuck to schedule. Most importantly, I got a high quality design at the end of the project. I highly recommend Rowan if you are looking for a quality mechanical engineer/CAD expert for your next project."</p>
<div class="abs avatar" role="img" aria-label="Small round customer portrait"></div>
<div class="abs author">Marta</div>
<div class="abs role">Manager</div>
<svg class="abs arrow" style="left:56px;top:3243px" viewBox="0 0 30 40"><path d="M22 4L8 20l14 16" stroke="#222" stroke-width="6" fill="none"/></svg>
<svg class="abs arrow" style="left:1113px;top:3243px" viewBox="0 0 30 40"><path d="M8 4l14 16L8 36" stroke="var(--blue)" stroke-width="6" fill="none"/></svg>

<!-- Footer -->
<footer class="abs footer"></footer>
<div class="abs contact-ic" style="left:143px;top:3652px"><svg width="22" height="28" viewBox="0 0 22 28"><path d="M11 0a11 11 0 0 0-11 11c0 8 11 17 11 17s11-9 11-17A11 11 0 0 0 11 0zm0 15a4 4 0 1 1 0-8 4 4 0 0 1 0 8z" fill="#fff"/></svg></div>
<div class="abs" style="left:239px;top:3636px"><div class="contact-label">Address :</div><div class="contact-text" style="margin-top:8px">We're based in South<br>Wales, UK.</div></div>
<div class="abs contact-ic" style="left:477px;top:3652px"><svg width="24" height="24" viewBox="0 0 24 24"><path fill="#fff" d="M6.6 10.8a15 15 0 0 0 6.6 6.6l2.2-2.2a1 1 0 0 1 1-.25 11.4 11.4 0 0 0 3.6.57 1 1 0 0 1 1 1V20a1 1 0 0 1-1 1A17 17 0 0 1 3 4a1 1 0 0 1 1-1h3.5a1 1 0 0 1 1 1c0 1.25.2 2.45.57 3.57a1 1 0 0 1-.25 1z"/></svg></div>
<div class="abs" style="left:573px;top:3636px"><div class="contact-label">Phone :</div><div class="contact-text" style="margin-top:8px">+44 (0)7900 314 622</div></div>
<div class="abs contact-ic" style="left:809px;top:3652px"><svg width="26" height="20" viewBox="0 0 26 20"><rect width="26" height="20" rx="2" fill="#fff"/><path d="M1 2l12 9 12-9" stroke="var(--blue)" stroke-width="2.5" fill="none"/></svg></div>
<div class="abs" style="left:905px;top:3636px"><div class="contact-label">Email :</div><div class="contact-text" style="margin-top:8px">info@valtorix.design</div></div>
<nav class="abs foot-nav"><span>Home</span><span class="sep"></span><span>Portfolio</span><span class="sep"></span><span>Our Services</span><span class="sep"></span><span>Contact Us</span><span class="sep"></span><span>Privacy Policy</span></nav>
<p class="abs copy center">© 2025 Valtorix Mechanical Design.</p>
<div class="abs up"><svg width="14" height="10" viewBox="0 0 14 10"><path d="M1 8l6-6 6 6" stroke="#fff" stroke-width="2.5" fill="none"/></svg></div>

</body>
</html>
```